zAvora Corporate Website

zAvora is a well-funded start up developing an Online Marketing Platform for small businesses in Europe.
We are launching in February 2012 with all-in-one online marketing services including professional website, DIY SEO, Dashboard with Reports and Online marketing tools, and Support.
Our internal web designer has come up with a preliminary website design which we wish to continue to improve using new ideas, colours, layout, image, etc.
The brief is very simple - improve the website whether it is look & feel, ease of use, conversion rate - we are looking for overall improvements.
The contest will last 5 days and we will award the winner £300.
If you are the winner , you will also be required to provide designs for 3 more internal pages adhering to the proposed home page design.
Judging criteria : -
Visual Design
Layout must adhere to best practices and wire frame. If you decide to move elements around significantly please provide reason
Functional, informative and drives calls to action
Industry/Entity Type
Marketing
Look and feel
Each slider illustrates characteristics of the customer's brand and the style your logo design should communicate.

```html
<!DOCTYPE html>
<html lang="en">
<head>
<meta charset="utf-8">
<title>zAvora – Online Marketing for Small Business</title>
<link href="https://fonts.googleapis.com/css2?family=Ubuntu:wght@400;500&family=Open+Sans:wght@300;400;600;700&family=Oswald:wght@400;500;600&display=swap" rel="stylesheet">
<style>
:root{
  --brand:#1a8fe0;
  --brand-dark:#0a5fd0;
  --link:#2aa0e6;
  --ink:#222;
  --text:#3a3a3a;
  --muted:#666;
  --page-top:#dde9f6;
  --page:#f2f5f9;
  --card:#f5f7fa;
  --card-line:#e1e5ea;
  --footer:#2b2b2b;
  --footer-line:#3c3c3c;
  --footer-text:#c9c9c9;
}
*{margin:0;padding:0;box-sizing:border-box}
html,body{width:818px;height:1200px;overflow:hidden}
body{position:relative;font-family:"Open Sans",Arial,sans-serif;color:var(--text);
  background:linear-gradient(180deg,var(--page-top) 0,var(--page) 260px,var(--page) 100%)}
.abs{position:absolute}
a{color:inherit;text-decoration:none}

/* header */
.top-links{top:9px;left:559px;font-size:7px;color:#444;letter-spacing:.2px}
.top-links span{margin:0 6px;color:#777}
.logo{top:32px;left:109px;display:flex;align-items:center;gap:8px}
.logo-dot{width:40px;height:40px;border-radius:50%;background:var(--brand)}
.logo-name{font-family:"Ubuntu",sans-serif;font-size:36px;font-weight:400;color:var(--ink);line-height:1}
.main-nav{top:52px;left:547px;width:160px;height:25px;border-radius:4px;display:flex;align-items:center;
  background:linear-gradient(#f4f4f4,#d8d8d8);font-size:8.5px;color:#333;box-shadow:0 1px 2px rgba(0,0,0,.2);overflow:hidden}
.main-nav .home{width:40px;height:100%;background:linear-gradient(#3aa4f5,#0c6fd6);display:flex;align-items:center;justify-content:center}
.main-nav a{padding:0 8px}
.main-nav .sep{width:1px;height:14px;background:#aaa}

/* hero */
.hero{top:99px;left:103px;width:611px;height:233px;border-radius:5px;overflow:hidden;
  background:linear-gradient(160deg,#3a8cf5 0%,#1c66e6 55%,#0f4fd0 100%);box-shadow:0 8px 10px -6px rgba(0,0,0,.35)}
.hero h1{position:absolute;top:12px;left:31px;font-size:20.5px;line-height:23px;font-weight:700;color:#fff;text-shadow:0 1px 2px rgba(0,0,0,.4)}
.hero ul{position:absolute;top:74px;left:33px;list-style:none}
.hero li{display:flex;align-items:center;gap:14px;height:23px;font-size:13.5px;font-weight:700;color:#fff}
.hero-cta{position:absolute;top:179px;left:69px;width:108px;height:37px;border-radius:5px;text-align:center;color:#fff;
  background:linear-gradient(#ffb31a,#ff7a00);border:1px solid #ffcf6a;box-shadow:0 2px 3px rgba(0,0,0,.3)}
.hero-cta small{display:block;font-size:8px;margin-top:3px}
.hero-cta strong{display:block;font-size:15px;line-height:17px}
.hero-art{position:absolute;left:313px;top:81px;width:298px;height:152px;
  background:radial-gradient(ellipse at 75% 60%,#7aa6e0 0%,#3d7de8 45%,rgba(40,110,235,0) 75%)}

/* intro */
.intro{top:368px;left:0;width:818px;text-align:center}
.intro h2{font-weight:300;font-size:19.5px;color:var(--ink)}
.intro h2 em{font-style:normal;color:var(--link)}
.intro p{font-weight:300;font-size:14px;color:#333}

/* offers */
.offer{top:439px;width:141px;height:95px;border-radius:3px;overflow:hidden;color:#fff;font-family:"Oswald",sans-serif;
  box-shadow:0 2px 3px rgba(0,0,0,.3)}
.offer .tag{position:absolute;top:9px;left:11px;font-size:17px;font-weight:600;line-height:18px}
.offer .big{position:absolute;top:27px;left:11px;font-size:22px;font-weight:600;line-height:22px;letter-spacing:.3px}
.offer .line{position:absolute;bottom:0;left:0;right:0;text-align:center;font-family:"Open Sans",sans-serif;font-size:8px;line-height:11px;padding:4px 0 5px}
.offer .ribbon{position:absolute;top:13px;right:-22px;width:86px;transform:rotate(55deg);background:linear-gradient(#2c8cf0,#1460c8);
  text-align:center;font-size:10px;line-height:14px;border-top:1px solid #fff;border-bottom:1px solid #fff}
.offer .pic{position:absolute;top:22px;left:94px;width:30px;height:26px;border-radius:3px}
.offer-free{left:109px;background:linear-gradient(#e62e1f,#a8150c)}
.offer-free .tag{color:#ffe23a}
.offer-free .line{font-family:"Oswald",sans-serif;font-size:12px;background:#2b2b2b}
.offer-pro{left:261px;background:linear-gradient(#ffb011,#e8620a)}
.offer-pro .tag{color:#fff36a}
.offer-pro .line{background:#7a3a08}
.offer-turbo{left:410px;background:linear-gradient(#5bbd2a,#2a7d10)}
.offer-turbo .line{background:none;font-size:8.5px;line-height:12px}
.sub{position:absolute;left:11px;font-size:7.5px;font-weight:600;color:#fff36a}

/* how it works */
.how{top:436px;left:570px;width:138px}
.how h3{font-family:"Oswald",sans-serif;font-weight:500;font-size:12px;color:var(--link)}
.how p{font-size:7.3px;line-height:11.6px;color:#333;margin-top:6px;text-align:justify}

/* about */
.about{top:562px;left:109px;width:598px}
.about h2{font-weight:400;font-size:18px;color:var(--link);margin-left:1px}
.about p{font-size:7.2px;line-height:11.6px;color:#333;margin-top:8px}
.about p + p{margin-top:11px}
.about b{font-weight:400;color:var(--link)}

/* feature cards */
.feature{top:732px;width:140px;height:64px;background:var(--card);border:1px solid var(--card-line);border-radius:3px}
.feature svg{position:absolute;left:6px;top:14px}
.feature h4{position:absolute;left:38px;top:9px;font-weight:400;font-size:13px;color:var(--link)}
.feature p{position:absolute;left:38px;top:29px;width:96px;font-size:7px;line-height:9.5px;color:#555}

/* gallery */
.gallery-text{top:855px;left:129px;width:145px}
.gallery-text h3{font-weight:400;font-size:11.5px;line-height:12px;color:var(--link);white-space:nowrap}
.gallery-text p{font-size:7.3px;line-height:11.6px;color:#444;margin-top:11px}
.view-more{top:959px;left:212px;font-size:7.5px;color:var(--link);display:flex;align-items:center;gap:4px}
.view-more i{width:8px;height:8px;border-radius:50%;border:1px solid #aaa;display:inline-block}
.shot{border:1px solid #ccc}
.shot-left{top:833px;left:321px;width:50px;height:130px;background:linear-gradient(#e8e8e8,#cfd3d8)}
.shot-right{top:833px;left:605px;width:61px;height:130px;background:linear-gradient(#2a2a2a,#3b5f8e 60%,#f0f0f0 60%)}
.shot-main{top:827px;left:369px;width:237px;height:141px;border:3px solid #2aa0e6;
  background:linear-gradient(#222 0,#333 30px,#eee 30px,#fff 100%)}

/* footer */
.footer{top:1000px;left:0;width:818px;height:200px;background:var(--footer);border-top:3px solid #4aa6e8}
.badge{top:990px;left:102px;width:116px;height:152px;color:#fff;font-size:7.2px;line-height:11.5px;
  background:linear-gradient(#5cb6ee,#1a7fd0);clip-path:polygon(0 0,100% 0,100% 100%,50% 93%,0 100%)}
.badge .name{display:flex;align-items:center;gap:5px;margin:17px 0 8px 8px;font-family:"Ubuntu",sans-serif;font-size:21px;color:#222}
.badge .name i{width:20px;height:20px;border-radius:50%;background:#222;display:block}
.badge address{font-style:normal;padding-left:11px}
.fcol{top:1025px}
.fcol h5{display:flex;align-items:center;gap:10px;font-weight:400;font-size:12px;color:#eee;height:22px;
  padding-bottom:4px;border-bottom:1px solid var(--footer-line);width:118px}
.fcol ul{list-style:none;margin-top:5px}
.fcol li{font-size:7.3px;color:var(--footer-text);height:19px;line-height:19px;border-bottom:1px solid var(--footer-line);width:118px;padding-left:8px;position:relative}
.fcol li::before{content:"";position:absolute;left:1px;top:8px;border:2px solid transparent;border-left-color:#4aa6e8}
.subscribe-box{top:1066px;left:608px;width:103px;height:16px;background:#fff;border-radius:2px;font-size:6.5px;color:#aaa;line-height:16px;padding-left:5px}
.subscribe-btn{top:1066px;left:694px;width:17px;height:16px;background:var(--brand);color:#fff;font-size:13px;line-height:15px;text-align:center;border-radius:0 2px 2px 0}
.follow{top:1104px;left:610px;font-size:11.5px;color:var(--link)}
.social{top:1124px;width:20px;height:20px;border-radius:50%;background:#e9e9e9;border:2px solid #fff}
.like{top:1157px;left:613px;width:46px;height:12px;display:flex;gap:3px}
.like i{display:block;background:#e6ebf3;border:1px solid #99a;width:30px}
.like b{display:block;background:#fff;border:1px solid #999;width:13px}
.copyright{top:1164px;left:0;width:818px;text-align:center;font-size:7.3px;color:#bbb}
.copyright b{font-weight:400;color:var(--link)}
</style>
</head>
<body>

<nav class="abs top-links"><a>ABOUT US</a><span>|</span><a>CONTACT US</a><span>|</span><a>LOGIN</a></nav>
<div class="abs logo"><span class="logo-dot"></span><span class="logo-name">zAvora</span></div>
<nav class="abs main-nav">
  <span class="home"><svg width="16" height="14" viewBox="0 0 16 14"><path d="M8 1 1 7h2v6h4V9h2v4h4V7h2z" fill="#fff"/></svg></span>
  <a>Quick Tour</a><span class="sep"></span><a>Pricing</a>
</nav>

<section class="abs hero">
  <h1>Getting a website has never<br>been so simple</h1>
  <ul>
    <li><svg width="17" height="12" viewBox="0 0 17 12"><path d="M0 4h9V0l8 6-8 6V8H0z" fill="#fff"/></svg>Business Websites</li>
    <li><svg width="17" height="12" viewBox="0 0 17 12"><path d="M0 4h9V0l8 6-8 6V8H0z" fill="#fff"/></svg>Online Marketing</li>
    <li><svg width="17" height="12" viewBox="0 0 17 12"><path d="M0 4h9V0l8 6-8 6V8H0z" fill="#fff"/></svg>Dashboard Controls</li>
    <li><svg width="17" height="12" viewBox="0 0 17 12"><path d="M0 4h9V0l8 6-8 6V8H0z" fill="#fff"/></svg>Full Setup &amp; Support</li>
  </ul>
  <a class="hero-cta"><small>Sign up NOW for</small><strong>FREE!</strong></a>
  <div class="hero-art" role="img" aria-label="Illustration of a puzzled business owner surrounded by floating marketing labels such as PPC, SEO, hosting and reporting"></div>
</section>

<section class="abs intro">
  <h2>The Complete Online Marketing Solution for <em>Small Business Websites</em></h2>
  <p>“Get a big online presence and more sales leads in 30 minutes”</p>
</section>

<div class="abs offer offer-free">
  <div class="tag">Free</div><div class="big">SETUP</div>
  <div class="pic" role="img" aria-label="Crate with download arrow" style="background:#c9a066"></div>
  <div class="ribbon">£ 199 Value</div>
  <div class="line">WEB OFFER ONLY</div>
</div>
<div class="abs offer offer-pro">
  <div class="tag">Pro</div><div class="big">PACKAGE</div>
  <div class="sub" style="top:52px">Big online presence</div>
  <div class="pic" role="img" aria-label="Parcel box" style="background:#d9a45a"></div>
  <div class="ribbon">£ 22 /month</div>
  <div class="line">Bussiness Website &amp; Easy Dashboard</div>
</div>
<div class="abs offer offer-turbo">
  <div class="tag" style="color:#fff">TURBO SALES</div><div class="big" style="font-size:18px;top:28px">PRO PLUS</div>
  <div class="sub" style="top:49px">More sales LEADS</div>
  <div class="pic" role="img" aria-label="Figure with headset" style="background:#9fd27a"></div>
  <div class="ribbon">£ 29 /month</div>
  <div class="line">Bussiness Website,<br>Easy Dashboard &amp; ppc Sales</div>
</div>

<section class="abs how">
  <h3>How does it work?</h3>
  <p>Neque porro quisquam est qui dolorem ipsum quia dolor vel eum iriure dolor in hendrerit in vulputate velit dou site vesse molestie consequat, vel illumsit amet, adipisci velit"</p>
</section>

<section class="abs about">
  <h2>About Us</h2>
  <p><b>zAvora</b> will build your business website, optimise SEO marketing and make recommendations on best practices to help you win customers. Let our team of experts design a business website for you. Choose a business website from <b>zAvora's</b> broad array of fabulous, customisable business websites and our experts will have your business online in minutes. <b>zAvora</b> lets you create a professional business website without the need to know how to code or programme.</p>
  <p>Your business website comes with automatic Internet marketing, marketing on the Internet is easy with <b>zAvora</b>, we automatically optimise your site for SEO marketing and we can run Searchly ad campaigns when you need them. Get a business website with online marketing now. <b>zAvora</b> brings your Small Business Website to LIFE!</p>
  <p>View our example business websites above, watch the video demo to see how to make a business website or call us now and get your business marketing online today. The <b>zAvora</b> website builder gives you a professional online appearance - post your own images, give customers your latest news and create customer testimonials, it's the most complete online marketing solution for your business.</p>
</section>

<div class="abs feature" style="left:109px">
  <svg width="26" height="26" viewBox="0 0 26 26"><path d="M1 2v23h24" stroke="#2aa0e6" stroke-width="2" fill="none"/><rect x="4" y="6" width="4" height="18" fill="#2aa0e6"/><rect x="10" y="12" width="4" height="12" fill="#2aa0e6"/><rect x="16" y="16" width="4" height="8" fill="#2aa0e6"/></svg>
  <h4>Case Studies</h4><p>Read real stories about small businesses online</p>
</div>
<div class="abs feature" style="left:262px">
  <svg width="24" height="28" viewBox="0 0 24 28"><circle cx="12" cy="10" r="8" stroke="#2aa0e6" stroke-width="1.5" fill="none"/><path d="M9 18v4h6v-4M10 25h4" stroke="#2aa0e6" stroke-width="1.5" fill="none"/></svg>
  <h4>How to</h4><p>Learn from our online marketing tips for small business</p>
</div>
<div class="abs feature" style="left:415px">
  <svg width="28" height="26" viewBox="0 0 28 26"><rect x="1" y="3" width="18" height="13" rx="3" fill="#2aa0e6"/><path d="M5 16l-2 5 6-5" fill="#2aa0e6"/><rect x="10" y="9" width="17" height="12" rx="3" fill="#1a7fd0"/></svg>
  <h4>News &amp; Chatter</h4><p>Get up-to-date news and chatter about online marketing</p>
</div>
<div class="abs feature" style="left:569px">
  <svg width="26" height="28" viewBox="0 0 26 28"><rect x="10" y="1" width="6" height="3" fill="#2aa0e6"/><circle cx="13" cy="16" r="11" fill="#2aa0e6"/><circle cx="13" cy="16" r="8" fill="#fff"/><path d="M13 10v6l4 3" stroke="#2aa0e6" stroke-width="1.6" fill="none"/></svg>
  <h4>Demo</h4><p>Find out what zAvora can do for your business.</p>
</div>

<section class="abs gallery-text">
  <h3>View examples of our<br>stunning business websites</h3>
  <p>Duis autem vel eum iriure dolor in hendrerit in vulputate velit esse molestie consequat, vel illum dolore eu feugiat nulla facilisis at vero eros et accumsan. esse molestie.</p>
</section>
<a class="abs view-more"><i></i>View more</a>
<svg class="abs" style="top:884px;left:291px" width="14" height="28" viewBox="0 0 14 28"><path d="M14 0v28L0 14z" fill="#8a8f96"/></svg>
<svg class="abs" style="top:884px;left:685px" width="14" height="28" viewBox="0 0 14 28"><path d="M0 0v28l14-14z" fill="#7fc4ee"/></svg>
<div class="abs shot shot-left" role="img" aria-label="Example customer website screenshot"></div>
<div class="abs shot shot-right" role="img" aria-label="Example customer website screenshot"></div>
<div class="abs shot-main" role="img" aria-label="Featured example business website screenshot"></div>

<footer class="abs footer"></footer>
<div class="abs badge">
  <div class="name"><i></i>zAvora</div>
  <address>14 Linden Row, London<br>EC1V 4RT - Suite 12<br>Phone. 020-555-0148<br>Email. info@zavora.com<br>www.zavora.com</address>
</div>

<div class="abs fcol" style="left:226px;width:140px">
  <h5 style="width:140px"><svg width="20" height="20" viewBox="0 0 20 20"><circle cx="10" cy="10" r="7" fill="none" stroke="#888" stroke-width="4" stroke-dasharray="3 2.5"/><circle cx="10" cy="10" r="3" fill="#888"/></svg>OurServices</h5>
  <ul><li style="width:140px">Search Engine Optimization (SEO)</li><li style="width:140px">Social Media</li><li style="width:140px">Web Analytics</li></ul>
</div>
<div class="abs fcol" style="left:376px">
  <h5><svg width="20" height="22" viewBox="0 0 20 22"><rect x="2" y="1" width="16" height="20" rx="2" fill="#888"/><rect x="4" y="3" width="12" height="14" fill="#2b2b2b"/></svg>ContactUs</h5>
  <ul><li>Contact Us</li><li>Customer Support</li><li>Request a call back</li><li>FAQ's</li></ul>
</div>
<div class="abs fcol" style="left:491px">
  <h5><svg width="24" height="20" viewBox="0 0 24 20"><path d="M1 2h8l2 3h12v14H1z" fill="#888"/></svg>Navigation</h5>
  <ul><li>Site Map</li><li>Terms and Condition</li><li>Privacy &amp; Policy</li><li>Get in Touch</li></ul>
</div>
<div class="abs fcol" style="left:608px">
  <h5 style="width:103px"><svg width="26" height="18" viewBox="0 0 26 18"><rect x="1" y="1" width="24" height="16" fill="#888"/><path d="M1 1l12 9 12-9" stroke="#2b2b2b" stroke-width="1.5" fill="none"/></svg>Subscribe</h5>
</div>
<div class="abs subscribe-box">Type your email here</div>
<div class="abs subscribe-btn">+</div>
<div class="abs follow">Follow</div>
<div class="abs social" style="left:610px" role="img" aria-label="Social network link"></div>
<div class="abs social" style="left:642px" role="img" aria-label="Microblog link"></div>
<div class="abs social" style="left:672px" role="img" aria-label="News feed link"></div>
<div class="abs like" role="img" aria-label="Like counter"><i></i><b></b></div>

<p class="abs copyright">Copyright © 2011 zAvora Pvt. Ltd 2011 -  All rights reserved.  Managed by <b>zAvora</b>  &nbsp;|&nbsp;  Admin</p>

</body>
</html>
```